web hosting reseller site, E-COMMERCE FUNCTIONALITY, AND MONTHLY PAYMENT INTERGRATION

hie there , i need a web hosting reseller site , 5 pages seo friendly , responsive and mobile friendly, i have a seller domain , basic content uploaded , design theme . i will be selling web hosting packages and domain names , i will also offer web design services and development . my project is so simple , the basic pages have content submitted already ,etc HOME, ABOUT, CONTACT US, BLOG POST .
Target Market(s)
5
Industry/Entity Type
web hosting
Coding
Coded - Design and coding required
Number of Pages Required
5+ page
Font styles to use
Requirements
Must have
- e commerce functionality, blog post, knowledge base , faq ,
Should not have
- affiliate links , subscription plugins

```html
<!DOCTYPE html>
<html lang="en">
<head>
<meta charset="utf-8">
<title>Skynode — Web Hosting</title>
<link href="https://fonts.googleapis.com/css2?family=Noto+Serif:wght@400;700&family=Roboto:wght@400;500&display=swap" rel="stylesheet">
<style>
:root{
  --blue:#2478c4;
  --blue-deep:#2f78bd;
  --cyan:#0aa5e8;
  --btn:#1599df;
  --ink:#1d1d1d;
  --muted:#555;
  --green:#12a66a;
  --sky:#d7f1fb;
  --footer:#1d7be6;
  --line:#e3e3e3;
}
*{box-sizing:border-box;margin:0;padding:0}
html,body{width:1200px;height:4120px;overflow:hidden;background:#fff}
body{font-family:"Roboto",sans-serif;color:var(--ink);position:relative}
.serif{font-family:"Noto Serif",serif}
section,header,footer{position:relative;width:1200px}
.btn{display:inline-block;background:var(--btn);color:#fff;font-family:"Noto Serif",serif;font-weight:700;font-size:17px;padding:16px 18px;box-shadow:0 4px 8px rgba(0,0,0,.2);text-decoration:none}

/* top bar */
.topbar{height:53px;border-bottom:1px solid var(--line);display:flex;align-items:center;justify-content:space-between;padding:0 96px 0 97px}
.brand{font-family:"Noto Serif",serif;font-weight:700;color:var(--cyan);font-size:25px;letter-spacing:1px}
.top-links{display:flex;gap:26px;font-family:"Noto Serif",serif;font-size:15px;color:#333;align-items:center}
.top-links span{display:flex;align-items:center;gap:8px}
.nav{height:62px;border-bottom:1px solid var(--line);display:flex;align-items:center;justify-content:space-between;padding:0 96px 0 97px}
.nav ul{display:flex;list-style:none;gap:49px;font-family:"Noto Serif",serif;font-size:17px}
.helpline{display:flex;align-items:center;gap:14px;font-family:"Noto Serif",serif}
.helpline .ic{width:40px;height:40px;border-radius:50%;background:#1c63b6;display:flex;align-items:center;justify-content:center}
.helpline b{font-weight:400;font-size:16px;display:block}
.helpline small{font-size:13px;color:#333}

/* hero */
.hero{height:573px;background:linear-gradient(100deg,#8fd3ec 0%,#5cbde0 45%,#1682c9 100%);overflow:hidden}
.hero-photo{position:absolute;left:560px;top:0;width:640px;height:573px;background:radial-gradient(circle at 60% 45%,#7fd6f2 0%,#2596d0 45%,#0b5ea8 100%)}
.hero-text{position:absolute;left:97px;top:125px;width:420px}
.hero-text h2{font-family:"Noto Serif",serif;font-weight:400;font-size:34px;letter-spacing:1px}
.hero-text h1{font-family:"Noto Serif",serif;font-weight:700;font-size:78px;line-height:1;margin-top:6px;letter-spacing:1px}
.hero-text p{color:#fff;font-family:"Noto Serif",serif;font-size:15px;line-height:26px;margin:30px 0 40px}

/* services */
.services{height:552px;text-align:center}
.sec-title{font-family:"Noto Serif",serif;font-weight:700;color:var(--blue);font-size:29px;letter-spacing:1px}
.services .sec-title{padding-top:84px}
.services p{font-family:"Noto Serif",serif;font-size:18px;line-height:30px;width:1000px;margin:36px auto 0}
.svc-row{position:absolute;top:285px;left:99px;display:flex;gap:14px}
.svc{width:189px;height:182px;border:1px solid #ddd;border-radius:12px;display:flex;flex-direction:column;align-items:center;justify-content:flex-end;padding-bottom:14px;font-family:"Noto Serif",serif;font-size:16px;line-height:25px;color:#222}
.svc .icon{width:84px;height:84px;margin-bottom:14px;border-radius:10px}
.svc.active{background:var(--blue-deep);color:#fff;border-color:var(--blue-deep);box-shadow:0 8px 14px rgba(0,0,0,.25)}
.arrow-btn{position:absolute;top:372px;width:40px;height:40px;border-radius:50%;background:#fff;box-shadow:0 2px 6px rgba(0,0,0,.2);display:flex;align-items:center;justify-content:center}

/* about */
.about{height:483px;background:var(--blue-deep)}
.about-photo{position:absolute;left:0;top:0;width:571px;height:483px;background:linear-gradient(90deg,#0b1624,#2c4a6b 40%,#0f2237 70%,#33628f)}
.about-text{position:absolute;left:621px;top:50px;width:475px;color:#fff}
.about-text h2{font-family:"Noto Serif",serif;font-size:29px;letter-spacing:1px}
.about-text p{font-family:"Noto Serif",serif;font-size:15.5px;line-height:25.7px;text-align:justify;margin:26px 0 30px}

/* reviews */
.reviews{height:573px;overflow:hidden;text-align:center}
.reviews .sec-title{padding-top:78px}
.bar{width:44px;height:3px;background:var(--blue);margin:14px auto 0}
.rev-row{position:absolute;top:165px;left:-184px;display:flex;gap:22px}
.rev{width:298px;height:333px;background:#f4f4f4;border-radius:6px;text-align:left;padding:22px 26px}
.rev-head{display:flex;align-items:center;color:var(--green)}
.rev-head .big{font-size:44px;line-height:1;margin-right:16px}
.rev-head .stars{font-size:24px;letter-spacing:2px}
.rev-head .pct{margin-left:auto;font-size:20px}
.rev p{font-size:14px;line-height:23px;color:#444;margin:22px 0 12px 0;padding-left:2px}
.rev .gold{color:#f2a724;font-size:18px;letter-spacing:5px}
.rev .gold span{font-size:14px;color:#444;letter-spacing:0;margin-left:6px}
.rev .date{font-size:14px;color:#555;margin-top:12px}
.rev-arrow{position:absolute;top:286px;width:40px;height:40px;border-radius:6px;background:var(--blue-deep);display:flex;align-items:center;justify-content:center}

/* vision */
.vision{height:824px;background:var(--sky)}
.block-text h3{font-family:"Noto Serif",serif;font-weight:700;color:var(--blue);font-size:31px}
.block-text p{font-size:15px;line-height:25px;color:#444;margin:22px 0 22px}
.art{position:absolute;border-radius:50%}

/* faq */
.faq{height:627px;text-align:center}
.faq .sec-title{padding-top:84px;font-size:31px}
.faq-list{position:absolute;left:192px;top:160px;width:816px}
.faq-item{border:1px solid #ccc;border-radius:10px;height:54px;display:flex;align-items:center;justify-content:space-between;padding:0 22px;margin-bottom:13px;font-family:"Noto Serif",serif;font-weight:700;font-size:21px;box-shadow:0 2px 4px rgba(0,0,0,.12)}
.faq-item .sign{font-size:28px;font-weight:400}
.faq-item.open{background:var(--cyan);border-color:var(--cyan);color:#fff;height:149px;flex-direction:column;align-items:stretch;justify-content:flex-start;padding:16px 20px}
.faq-item.open .row{display:flex;justify-content:space-between;align-items:center}
.faq-item.open p{font-family:"Roboto",sans-serif;font-weight:400;font-size:12.5px;line-height:25px;text-align:left;margin-top:12px}

/* footer */
.footer{height:320px;background:linear-gradient(90deg,#1a74df,#2588ec);color:#fff}
.f-brand{position:absolute;left:96px;top:50px;width:380px}
.f-brand .brand{color:#fff;font-size:62px;letter-spacing:2px}
.f-brand p{font-size:15px;line-height:26px;margin-top:12px}
.social{display:flex;gap:20px;margin-top:20px}
.social i{width:22px;height:22px;border:1px solid #fff;border-radius:50%;display:block}
.f-col{position:absolute;top:54px}
.f-col h4{font-family:"Noto Serif",serif;font-weight:400;font-size:17px;letter-spacing:1px;margin-bottom:24px}
.f-col li{list-style:none;font-size:16px;line-height:32.5px}
.contact li{display:flex;gap:14px;font-size:15px;line-height:25px;margin-bottom:24px}
.copy{height:53px;background:#222;color:#fff;font-size:16px;display:flex;align-items:center;justify-content:center}
</style>
</head>
<body>

<header>
  <div class="topbar">
    <div class="brand">SKYNODE</div>
    <div class="top-links">
      <span><svg width="14" height="12" viewBox="0 0 14 12"><path d="M1 1h12v7H5l-3 3V8H1z" fill="#222"/></svg>Chat</span>
      <span><svg width="13" height="13" viewBox="0 0 13 13"><circle cx="6.5" cy="4" r="3" fill="#222"/><path d="M1 13c0-4 11-4 11 0z" fill="#222"/></svg>Login</span>
      <span><svg width="20" height="20" viewBox="0 0 20 20"><circle cx="10" cy="10" r="9" fill="#c9d6ee"/></svg>INR</span>
    </div>
  </div>
  <nav class="nav">
    <ul><li>Home</li><li>About Us</li><li>Services</li><li>Programs</li><li>Contact</li></ul>
    <div class="helpline">
      <div class="ic"><svg width="18" height="18" viewBox="0 0 24 24"><path d="M6.6 10.8a15 15 0 006.6 6.6l2.2-2.2c.3-.3.7-.4 1-.2 1.1.4 2.3.6 3.6.6.6 0 1 .4 1 1V20c0 .6-.4 1-1 1A17 17 0 013 4c0-.6.4-1 1-1h3.5c.6 0 1 .4 1 1 0 1.3.2 2.5.6 3.6.1.3 0 .7-.2 1z" fill="#fff"/></svg></div>
      <div><b>+1 555-010-0199</b><small>(24x7 Help-line)</small></div>
    </div>
  </nav>
</header>

<section class="hero">
  <div class="hero-photo" role="img" aria-label="Smiling man in a blue shirt and tie working on a laptop, set against a glowing blue cloud and binary-code backdrop"></div>
  <div class="hero-text">
    <h2>WELCOME TO</h2>
    <h1>SKYNODE</h1>
    <p>Lorem ipsum dolor sit amet, consectetur adipiscing elit, sed do eiusmod tempor incididunt ut labore et dolore magna aliqua.</p>
    <a class="btn">GET STARTED</a>
  </div>
</section>

<section class="services">
  <h2 class="sec-title">OUR SERVICES</h2>
  <p>Free SSL Access Management eCommerce Optimization Free Migration Backups EdgeShield CDN &amp; DDoS Protection TurboSpeed PressCMS Module One-Click PressCMS Installation 24/7/365 Tech Support Auto Script Installer 99.9% Uptime Guarantee</p>
  <div class="arrow-btn" style="left:49px"><svg width="12" height="14" viewBox="0 0 12 14"><path d="M8 1L2 7l6 6" stroke="#2478c4" stroke-width="2" fill="none"/></svg></div>
  <div class="arrow-btn" style="left:1116px"><svg width="12" height="14" viewBox="0 0 12 14"><path d="M4 1l6 6-6 6" stroke="#2478c4" stroke-width="2" fill="none"/></svg></div>
  <div class="svc-row">
    <div class="svc active"><div class="icon" role="img" aria-label="Globe above server racks icon" style="background:linear-gradient(#3da4e6,#1b3c63)"></div>WEB HOSTING</div>
    <div class="svc"><div class="icon" style="background:#4a8ee0"></div>PRESSCMS<br>HOSTING</div>
    <div class="svc"><div class="icon" style="background:#efe9f3"></div>SHOPCMS<br>HOSTING</div>
    <div class="svc"><div class="icon" role="img" aria-label="Network of users icon" style="background:linear-gradient(#f2b32a,#2e73c8)"></div>RESELLER<br>HOSTING</div>
    <div class="svc"><div class="icon" role="img" aria-label="Cloud server icon" style="background:linear-gradient(#46b9c7,#f0c33a)"></div>CLOUD HOSTING</div>
  </div>
</section>

<section class="about">
  <div class="about-photo" role="img" aria-label="Rows of server racks in a blue-lit data centre"></div>
  <div class="about-text">
    <h2>ABOUT US</h2>
    <p>A Unique Team Behind Your Online Success What makes Skynode unique is our extraordinary team of individuals who put their passion, dedication, and expertise into taking care of our customers' websites. We love what we do and we are motivated to deliver an outstanding level of service. Expert And Friendly Hosting Support Our support team is famous for being fast, friendly and helpful. Every year, our customers confirm this fact giving us many five-star reviews and satisfaction rates close to 100%.</p>
    <a class="btn">READ MORE</a>
  </div>
</section>

<section class="reviews">
  <h2 class="sec-title">SKYNODE WEB HOSTING REVIEWS</h2>
  <div class="bar"></div>
  <div class="rev-row">
    <div class="rev"></div>
    <div class="rev"><div class="rev-head"><span class="big">★</span><span class="stars">★★★★★</span><span class="pct">98%</span></div><p>We get hundreds of five-star ratings and the quality of our service gets praised all over. Read here what real customers have to say about our hosting, why they rate our service high, and what makes us different from the rest.</p><div class="gold">★★★★★<span>(5-star ratings)</span></div><div class="date">📅 (June2022)</div></div>
    <div class="rev"><div class="rev-head"><span class="big">★</span><span class="stars">★★★★★</span><span class="pct">98%</span></div><p>We get hundreds of five-star ratings and the quality of our service gets praised all over. Read here what real customers have to say about our hosting, why they rate our service high, and what makes us different from the rest.</p><div class="gold">★★★★★<span>(5-star ratings)</span></div><div class="date">📅 (June2022)</div></div>
    <div class="rev"><div class="rev-head"><span class="big">★</span><span class="stars">★★★★★</span><span class="pct">98%</span></div><p>We get hundreds of five-star ratings and the quality of our service gets praised all over. Read here what real customers have to say about our hosting, why they rate our service high, and what makes us different from the rest.</p><div class="gold">★★★★★<span>(5-star ratings)</span></div><div class="date">📅 (June2022)</div></div>
    <div class="rev" style="opacity:.6"><div class="rev-head"><span class="big">★</span><span class="stars">★★★★★</span></div><p>We get hundreds of five-star ratings and the quality of our service gets praised all over.</p></div>
  </div>
  <div class="rev-arrow" style="left:100px"><svg width="10" height="14" viewBox="0 0 10 14"><path d="M8 1L2 7l6 6" stroke="#fff" stroke-width="2" fill="none"/></svg></div>
  <div class="rev-arrow" style="left:1053px"><svg width="10" height="14" viewBox="0 0 10 14"><path d="M2 1l6 6-6 6" stroke="#fff" stroke-width="2" fill="none"/></svg></div>
</section>

<section class="vision">
  <div class="block-text" style="position:absolute;left:96px;top:80px;width:460px">
    <h3>Our vision and mission</h3>
    <p>We believe in a world where people have the freedom to choose how their digital content is shared, and we foster their success by providing an open web platform of choice.</p>
    <a class="btn">READ MORE</a>
  </div>
  <div class="art" style="left:790px;top:54px;width:310px;height:310px;background:#bfe2f4"></div>
  <div style="position:absolute;left:694px;top:54px;width:290px;height:290px;border-radius:16px;background:linear-gradient(#1fa6ee 0%,#1fa6ee 40%,#12365a 55%,#12365a 100%)" role="img" aria-label="Illustration of a globe connected to a row of server units"></div>

  <div class="art" style="left:90px;top:440px;width:320px;height:320px;background:#bfe2f4"></div>
  <div style="position:absolute;left:225px;top:460px;width:310px;height:310px;border-radius:16px;background:linear-gradient(160deg,#ffb020,#f7c59a 55%,#17b05c)" role="img" aria-label="Illustration of a gold dollar coin dropping into an open hand with a green arrow"></div>
  <div class="block-text" style="position:absolute;left:645px;top:466px;width:460px">
    <h3>Money-Back Guarantee</h3>
    <p>Try us and love us, or get a refund within 30 days of signing up. Your satisfaction is our top priority and we're confident you'll be pleased with our services</p>
    <a class="btn">READ MORE</a>
  </div>
</section>

<section class="faq">
  <h2 class="sec-title">FAQ</h2>
  <div class="bar" style="margin-top:10px"></div>
  <div class="faq-list">
    <div class="faq-item open"><div class="row"><span>SED UT PERSPICIATIS</span><span class="sign">−</span></div><p>Lorem ipsum dolor sit amet, consectetur adipiscing elit, sed do eiusmod tempor incididunt ut labore et dolore magna aliqua. Ut enim ad minim veniam, quis nostrud exercitation ullamco laboris nisi ut aliquip ex ea commodo consequat. Duis aute irure dolor in reprehenderit in voluptate velit esse cillum dolore eu fugiat nulla pariatur.</p></div>
    <div class="faq-item"><span>SED UT PERSPICIATIS</span><span class="sign">+</span></div>
    <div class="faq-item"><span>SED UT PERSPICIATIS</span><span class="sign">+</span></div>
    <div class="faq-item"><span>SED UT PERSPICIATIS</span><span class="sign">+</span></div>
    <div class="faq-item"><span>SED UT PERSPICIATIS</span><span class="sign">+</span></div>
  </div>
</section>

<footer class="footer">
  <div class="f-brand">
    <div class="brand">SKYNODE</div>
    <p>Lorem ipsum dolor sit amet, consectetur adipiscing elit, sed do eiusmod tempor incididunt ut labore et dolore magna aliqua.</p>
    <div class="social"><i></i><i></i><i></i></div>
  </div>
  <div class="f-col" style="left:515px"><h4>QUICK LINK</h4><ul><li>Home</li><li>About</li><li>Services</li><li>Programs</li><li>Contact</li></ul></div>
  <div class="f-col contact" style="left:699px"><h4>CONTACT</h4><ul>
    <li><svg width="12" height="16" viewBox="0 0 12 16"><path d="M6 0a6 6 0 016 6c0 4-6 10-6 10S0 10 0 6a6 6 0 016-6z" fill="#fff"/><circle cx="6" cy="6" r="2" fill="#1f7de6"/></svg><span>1471 Sed ut perspiciatis unde<br>natus error sit</span></li>
    <li><svg width="14" height="14" viewBox="0 0 24 24"><path d="M6.6 10.8a15 15 0 006.6 6.6l2.2-2.2c.3-.3.7-.4 1-.2 1.1.4 2.3.6 3.6.6.6 0 1 .4 1 1V20c0 .6-.4 1-1 1A17 17 0 013 4c0-.6.4-1 1-1h3.5c.6 0 1 .4 1 1 0 1.3.2 2.5.6 3.6.1.3 0 .7-.2 1z" fill="#fff"/></svg><span>+1 555 010 0199</span></li>
    <li><svg width="16" height="12" viewBox="0 0 16 12"><rect x="1" y="1" width="14" height="10" fill="none" stroke="#fff" stroke-width="1.5"/><path d="M1 1l7 6 7-6" fill="none" stroke="#fff" stroke-width="1.5"/></svg><span>info@skynode.example</span></li>
  </ul></div>
  <div class="f-col" style="left:956px"><h4>HELP LINK</h4><ul><li>Terms &amp; Conditions</li><li>Privacy Policy</li><li>About Us</li><li>Support</li></ul></div>
</footer>
<div class="copy">© copyrights 2022&nbsp; Skynode | All Rights Reserved</div>

</body>
</html>
```